Business card for a Exhibition booth fabrication company

Hi. My company would like to change our corporate name card. We are an events and Exhibition stand builder company. We would like our corporate name card to resonate what we do. I need someone to create something unique that relates to the industry that I am in. The graphic designer should be creative to incorporate the elements of my industry and try to blend in well in the design of the card. Our aim is to ensure that we are unique and our card can look different from our competitors.
Updates

Target Market(s)

Marketing and events manager from all companies

Contact Information for Business Card

The business card should have the following details:
Name
Job Title
Email
Website

Colors

Designer to choose colors to be used in the design.

Requirements
Must have
• The card must be look something that is relevant to the service that I am providing. My website is: www.velmora-buildworks.com
• You can see my website to get more information on what service that I am doing
Nice to have
• On the back of my card, I would like to have a globe image with the incorporation of my company logo. This is to indicate that my services can be done in any part of the world.

```html
<!DOCTYPE html>
<html lang="en">
<head>
<meta charset="utf-8">
<title>Velmora Buildworks – Business Card</title>
<link rel="stylesheet" href="https://fonts.googleapis.com/css2?family=Open+Sans:wght@400;600;700&display=swap">
<style>
  :root {
    --bg-light: #dcdddf;
    --bg-dark: #9c9da0;
    --card-white: #ffffff;
    --brand-red: #ed1c24;
    --brand-grey: #636466;
    --text-grey: #58595b;
    --divider: #c9c9cb;
    --map-light: #8a8b8e;
    --map-mid: #7a7b7e;
    --mark-grey: #b3b4b6;
  }
  * { margin: 0; padding: 0; box-sizing: border-box; }
  html, body {
    width: 1200px;
    height: 1118px;
    overflow: hidden;
  }
  body {
    background: linear-gradient(90deg, var(--bg-light) 0%, #bfc0c3 55%, var(--bg-dark) 100%);
    font-family: "Open Sans", Arial, sans-serif;
  }
  .stage {
    position: relative;
    width: 1121px;
    height: 1044px;
    transform: scale(1.0705);
    transform-origin: 0 0;
  }
  .card {
    position: absolute;
    left: 208px;
    width: 704px;
    height: 402px;
    border-radius: 30px;
    overflow: hidden;
  }
  .card--front { top: 85px; background: var(--card-white); }
  .card--back { top: 542px; height: 403px; background: var(--brand-grey); }

  .card__waves {
    position: absolute;
    left: 0; top: 0;
    width: 704px; height: 402px;
  }

  .brand {
    position: absolute;
    left: 40px;
    top: 158px;
    display: flex;
    align-items: center;
    gap: 10px;
  }
  .brand__dot {
    width: 14px; height: 14px;
    border-radius: 50%;
    background: var(--brand-red);
  }
  .brand__name {
    font-size: 21px;
    font-weight: 600;
    letter-spacing: 1.5px;
    color: var(--text-grey);
    white-space: nowrap;
  }

  .divider {
    position: absolute;
    left: 379px;
    top: 78px;
    width: 2px;
    height: 212px;
    background: var(--divider);
  }

  .contact {
    position: absolute;
    left: 397px;
    top: 70px;
    color: var(--text-grey);
  }
  .contact__name {
    font-size: 24px;
    font-weight: 700;
    color: var(--brand-red);
    letter-spacing: 0.5px;
    line-height: 30px;
  }
  .contact__title {
    font-size: 18px;
    letter-spacing: 1px;
    line-height: 26px;
    margin-bottom: 14px;
  }
  .contact__address {
    font-size: 16.5px;
    line-height: 24px;
    margin-bottom: 14px;
  }
  .contact__list { list-style: none; }
  .contact__item {
    display: flex;
    align-items: center;
    gap: 12px;
    font-size: 16.5px;
    line-height: 32px;
  }
  .contact__icon { width: 17px; height: 17px; flex: none; }

  .world-map {
    position: absolute;
    left: 0;
    top: 70px;
    width: 704px;
    height: 272px;
    background: radial-gradient(ellipse at 50% 45%, var(--map-light) 0%, var(--map-mid) 55%, rgba(99,100,102,0) 85%);
  }
  .back-mark {
    position: absolute;
    left: 0; right: 0;
    top: 182px;
    text-align: center;
    font-size: 34px;
    font-weight: 700;
    letter-spacing: 2px;
    color: var(--mark-grey);
  }
  .back-web {
    position: absolute;
    left: 0; right: 0;
    top: 362px;
    text-align: center;
    font-size: 19px;
    letter-spacing: 3.4px;
    color: var(--card-white);
  }
</style>
</head>
<body>
<div class="stage">

  <section class="card card--front" aria-label="Card front">
    <svg class="card__waves" viewBox="0 0 704 402" aria-hidden="true">
      <path d="M0 277 Q250 350 515 375 Q240 372 0 318 Z" fill="var(--brand-grey)"/>
      <path d="M0 321 Q300 378 625 367 L530 402 L0 402 Z" fill="var(--brand-red)"/>
      <path d="M546 402 L704 342 L704 402 Z" fill="var(--brand-grey)"/>
    </svg>

    <div class="brand">
      <span class="brand__dot"></span>
      <span class="brand__name">VELMORA BUILDWORKS</span>
    </div>

    <div class="divider"></div>

    <div class="contact">
      <p class="contact__name">DANIEL HARTWELL</p>
      <p class="contact__title">PRESIDENT</p>
      <p class="contact__address">Street Name, City Name<br>Zipcode - 01234</p>
      <ul class="contact__list">
        <li class="contact__item">
          <svg class="contact__icon" viewBox="0 0 24 24" aria-hidden="true"><path fill="var(--brand-red)" d="M6.6 10.8a15.1 15.1 0 0 0 6.6 6.6l2.2-2.2c.3-.3.7-.4 1-.2 1.1.4 2.3.6 3.6.6.6 0 1 .4 1 1V20c0 .6-.4 1-1 1A17 17 0 0 1 3 4c0-.6.4-1 1-1h3.5c.6 0 1 .4 1 1 0 1.3.2 2.5.6 3.6.1.3 0 .7-.2 1z"/></svg>
          <span>012-345-6789</span>
        </li>
        <li class="contact__item">
          <svg class="contact__icon" viewBox="0 0 24 24" aria-hidden="true"><rect x="2" y="5" width="20" height="14" fill="var(--brand-red)"/><path d="M2 5 L12 13 L22 5 M2 19 L9.5 11.5 M22 19 L14.5 11.5" stroke="#fff" stroke-width="1.5" fill="none"/></svg>
          <span>info@velmora-buildworks.com</span>
        </li>
        <li class="contact__item">
          <svg class="contact__icon" viewBox="0 0 24 24" aria-hidden="true"><g fill="none" stroke="var(--brand-red)" stroke-width="1.8"><circle cx="12" cy="12" r="9.5"/><ellipse cx="12" cy="12" rx="4.2" ry="9.5"/><path d="M2.5 12h19M4 7h16M4 17h16"/></g></svg>
          <span>www.velmora-buildworks.com</span>
        </li>
      </ul>
    </div>
  </section>

  <section class="card card--back" aria-label="Card back">
    <div class="world-map" role="img" aria-label="World map spanning the card"></div>
    <p class="back-mark">VELMORA BUILDWORKS</p>
    <p class="back-web">www.velmora-buildworks.com</p>
  </section>

</div>
</body>
</html>
```